New Corporate Email Signature with Custom GIF KAV Electric LLC & KAV Fire & Security

Project Overview
KAV Electric LLC and KAV Fire & Security are seeking a professional, polished, and technically robust corporate email signature design. The project has two integrated deliverables:
A custom animated GIF representing both sides of our business
A complete corporate email signature layout designed for real-world compatibility (Gmail, Outlook, iOS, Android)
Our brand aesthetic is corporate, conservative, and clean. We value clarity, trust, professionalism, and subtle creativity β€” nothing overly flashy or cartoonish.
This design will be used across the entire company and must be visually aligned with our brand while remaining technically dependable.

PART 1 β€” Animated GIF Requirements
The GIF will be the core visual anchor of the new signature.
It must be clean, smooth, subtle, and optimized for email use.
βš™ Technical Requirements
Max file size: 150–200 KB (smaller is better)
Dimensions: approx 300px width (flexible, but must look good small)
Looping: continuous loop
Style: professional, minimalistic transitions

No rapid flashing or harsh animations
Must export cleanly into a format email clients accept

🎞 GIF Animation Sequence
Phase 1 β€” KAV Electric (KE)
Use the yellow β€œKE” avatar logo (provided).
Animation flow:
KE avatar appears
Full name β€œKAV Electric LLC” slides in, fades in, or otherwise appears smoothly
A scrolling or cycling list of service offerings displays:
EV Charging Stations
Generator & Transformers
Testing & Troubleshooting
LED Lighting Upgrades
After the list is shown, the entire KE segment fades out

Phase 2 β€” KAV Fire & Security (KF)
Use the red β€œKF” avatar logo (provided).
Animation flow mirrors Phase 1:
KF avatar appears
Full name β€œKAV Fire & Security” slides/fades in
Scrolling or cycling list of services displays:
Fire Alarm Upgrades
BQTL 48 Test & Inspect
Security Surveillance Systems
Access Control Systems
Data & Fiber Optic Cabling
Fade out β†’ loop back to KE
Creative Direction

Designers are encouraged to use:
Clean transitions
Soft fades
Professional typography
Modern minimalism
Consistent brand colors
High clarity at small sizes

Avoid:
Busy motion
Hard flashes
Excessive text overlays
Overly long transitions

The goal: a smooth, corporate-grade rotation that fits seamlessly into an email signature.

PART 2 β€” Corporate Email Signature Design

The signature must be visually appealing, brand-aligned, and structurally bulletproof across all major email systems.
πŸ“ Required Elements
πŸ‘€ Left Side Content
Circular headshot (we will supply final photos)
Social media icons with embedded URLs:
Facebook
LinkedIn
Google Business Profile
Instagram

Icons should be clean, modern, and in alignment with brand colors
πŸ“„ Right Side Content
Name
Title
KAV Electric LLC / KAV Fire & Security (depending on user)
Phone number
Email address
License# 52804
Physical office address: 384 Pembrook St, Westwood NJ 07912

Small CTA for newsletter signup (button or micro-banner)

🏒 Branding Assets Provided

You will receive:
KE avatar logo
KF avatar logo
Full-name KE logo
Full-name KF logo

These should be incorporated naturally and professionally.

Design Requirements

Conservative corporate styling

Clean typography

Balanced use of white space

Professional hierarchy

Light and dark mode compatibility preferred

Layout should not rely on one large image

All images should export cleanly for hosting on servers/CDN

Avoid overly tall signatures

The final signature must present as modern, trustworthy, and technically reliable across platforms.

πŸ§ͺ Compatibility Requirements

The signature must display correctly in:

Gmail (web and mobile)

Outlook (desktop & online)

Apple Mail

iPhone Mail

Android mail apps

Designers must avoid DIV-based layouts and instead propose a layout that can be implemented using table-based HTML, which is the industry standard for email compatibility.

You do not need to build the HTML β€” only supply the final layered design (PSD/AI/Figma) plus a clear structural layout that can be converted to HTML later.

πŸ“¦ Deliverables
1. Animated GIF

Final optimized GIF

Source file (After Effects, Photoshop, or equivalent)

Export guidelines so we can reproduce future versions

2. Email Signature Design

Full static design mockup

Modular layout for each employee

Icon set for social media

Newsletter CTA element

Clear spacing, alignment, and typography specifications

All source files (PSD, AI, Figma, etc.)

🧭 Creative Guidance Summary

We want:
βœ” Modern
βœ” Corporate
βœ” Minimalistic
βœ” Professional
βœ” Clean motion
βœ” Consistent branding
βœ” Email-safe elements

We do not want:
✘ Flashy marketing look
✘ Overly colorful or playful styles
✘ Hard-to-read fonts
✘ Heavy animation
✘ Oversized signatures

πŸ›  Tools & Format Flexibility

We allow full creative freedom regarding:

Animation style

Typography choices

Structuring of the two-column layout

How the service lists scroll or cycle

As long as the end result is clean, brand-aligned, professional, and email-compatible.

πŸ’¬ Final Note to Designers

We encourage creativity within the boundaries of corporate professionalism.
This signature will represent our company every time an email is sent β€” it must communicate trust, clarity, expertise, and brand strength.

```html
<!DOCTYPE html>
<html lang="en">
<head>
<meta charset="utf-8">
<title>KAV Electric LLC – Email Signature</title>
<link rel="stylesheet" href="https://fonts.googleapis.com/css2?family=Montserrat:wght@400;500;600;700;800&display=swap">
<style>
  :root {
    --brand-yellow: #f2c200;
    --photo-warm: #f5b51c;
    --ink: #4a4a4a;
    --ink-soft: #666666;
    --icon-grey: #6b6b6b;
    --paper: #ffffff;
  }
  html, body {
    margin: 0;
    padding: 0;
    overflow: hidden;
    background: var(--paper);
  }
  .signature {
    position: relative;
    width: 1200px;
    height: 400px;
    overflow: hidden;
    background: var(--paper);
    font-family: "Montserrat", Arial, sans-serif;
    color: var(--ink);
  }
  .side-band {
    position: absolute;
    left: 0; top: 0;
    width: 196px; height: 400px;
    background: var(--brand-yellow);
  }
  .headshot {
    position: absolute;
    left: 72px; top: 22px;
    width: 196px; height: 272px;
    border-radius: 98px;
    border: 7px solid var(--paper);
    box-shadow: 0 0 0 2px #d9d9d9;
    background: radial-gradient(circle at 50% 38%, #f9c649 0%, var(--photo-warm) 60%, #e79f12 100%);
    box-sizing: border-box;
  }
  .social {
    position: absolute;
    left: 78px; top: 318px;
    display: flex;
    gap: 34px;
  }
  .social-dot {
    width: 28px; height: 28px;
    border-radius: 50%;
    background: var(--icon-grey);
  }
  .person-name {
    position: absolute;
    left: 364px; top: 28px;
    margin: 0;
    font-size: 31px;
    font-weight: 700;
    letter-spacing: 0.5px;
    line-height: 1;
    color: var(--ink);
  }
  .person-title {
    position: absolute;
    left: 364px; top: 76px;
    margin: 0;
    font-size: 26px;
    font-weight: 500;
    line-height: 1;
    color: var(--ink-soft);
  }
  .company-name {
    position: absolute;
    left: 364px; top: 114px;
    margin: 0;
    font-size: 34px;
    font-weight: 800;
    letter-spacing: 5px;
    line-height: 1;
    text-transform: uppercase;
    color: var(--ink);
  }
  .contact-list {
    position: absolute;
    left: 364px; top: 171px;
    margin: 0; padding: 0;
    list-style: none;
  }
  .contact-item {
    display: flex;
    align-items: center;
    height: 38px;
    margin-bottom: 12px;
    font-size: 27px;
    font-weight: 500;
    color: var(--ink);
  }
  .contact-icon {
    width: 38px; height: 38px;
    margin-right: 16px;
    flex-shrink: 0;
  }
  .monogram {
    position: absolute;
    left: 930px; top: 18px;
    width: 210px;
    margin: 0;
    text-align: center;
    font-size: 108px;
    font-weight: 800;
    line-height: 1;
    color: var(--icon-grey);
  }
  .cta-join {
    position: absolute;
    left: 1036px; top: 304px;
    width: 142px; height: 58px;
    border-radius: 29px;
    background: var(--brand-yellow);
    color: var(--ink);
    font-size: 23px;
    font-weight: 700;
    display: flex;
    align-items: center;
    justify-content: center;
    text-decoration: none;
  }
  .version-tag {
    position: absolute;
    left: 1138px; top: 366px;
    font-size: 20px;
    font-weight: 500;
    color: var(--ink-soft);
  }
</style>
</head>
<body>
<div class="signature">
  <div class="side-band"></div>
  <div class="headshot" role="img" aria-label="Circular headshot of the employee"></div>

  <nav class="social" aria-label="Social profiles">
    <span class="social-dot" role="img" aria-label="Social profile link"></span>
    <span class="social-dot" role="img" aria-label="Social profile link"></span>
    <span class="social-dot" role="img" aria-label="Social profile link"></span>
    <span class="social-dot" role="img" aria-label="Social profile link"></span>
  </nav>

  <h1 class="person-name">MARCUS HALE</h1>
  <p class="person-title">Design Creator</p>
  <p class="company-name">KAV Electric LLC</p>

  <ul class="contact-list">
    <li class="contact-item">
      <svg class="contact-icon" viewBox="0 0 38 38" aria-hidden="true">
        <circle cx="19" cy="19" r="19" fill="var(--icon-grey)"/>
        <path d="M13 10.5c1-.6 2-.3 2.6.6l1.6 2.6c.5.8.3 1.8-.4 2.4l-1 .8c.9 2 2.6 3.8 4.6 4.8l.9-1c.6-.7 1.6-.9 2.4-.4l2.6 1.6c.9.6 1.2 1.7.6 2.6l-.9 1.4c-.8 1.2-2.3 1.8-3.7 1.3-5.3-1.8-9.5-6-11.2-11.3-.4-1.4.1-2.9 1.3-3.7z" fill="#fff"/>
      </svg>
      1-800 482 316
    </li>
    <li class="contact-item">
      <svg class="contact-icon" viewBox="0 0 38 38" aria-hidden="true">
        <circle cx="19" cy="19" r="19" fill="var(--icon-grey)"/>
        <rect x="10" y="12.5" width="18" height="13" rx="2" fill="#fff"/>
        <path d="M10.8 13.5l8.2 6.3 8.2-6.3" fill="none" stroke="var(--icon-grey)" stroke-width="1.8"/>
      </svg>
      info@kavelectricllc.com
    </li>
    <li class="contact-item">
      <svg class="contact-icon" viewBox="0 0 38 38" aria-hidden="true">
        <circle cx="19" cy="19" r="19" fill="var(--icon-grey)"/>
        <rect x="9.5" y="12" width="19" height="14" rx="2" fill="#fff"/>
        <circle cx="14.5" cy="17.5" r="2" fill="var(--icon-grey)"/>
        <path d="M11.8 23c.4-2 1.5-3 2.7-3s2.3 1 2.7 3z" fill="var(--icon-grey)"/>
        <rect x="19" y="16" width="7" height="1.6" fill="var(--icon-grey)"/>
        <rect x="19" y="19.5" width="5.5" height="1.6" fill="var(--icon-grey)"/>
      </svg>
      License# 52804
    </li>
    <li class="contact-item">
      <svg class="contact-icon" viewBox="0 0 38 38" aria-hidden="true">
        <circle cx="19" cy="19" r="19" fill="var(--icon-grey)"/>
        <path d="M19 9.5c-3.9 0-7 3-7 6.9 0 5 7 12.1 7 12.1s7-7.1 7-12.1c0-3.9-3.1-6.9-7-6.9z" fill="#fff"/>
        <circle cx="19" cy="16.4" r="2.6" fill="var(--icon-grey)"/>
      </svg>
      384 Pembrook St, Millbrook PA 19032
    </li>
  </ul>

  <p class="monogram">KE</p>

  <a class="cta-join" href="#newsletter">JOIN US</a>
  <span class="version-tag">M1</span>
</div>
</body>
</html>
```